Web Design for a Biotech Consulting Firm

We need a web site design for a new business based in Philadelphia called Verantel Dx. This is a consulting firm that will serve medical diagnostics industry, which is part of the life science/healthcare industry focusing on developing and marketing products that help in early detection, monitoring or management of diseases. Our consulting firm will help medical diagnostic companies to overcome key challenges in designing, evaluating and marketing new products.Our company name is Verantel Dx. Verantel is Latin word for "something" Dx represents diagnostics. The idea behind the name is that we help companies to transform the original, early product ideas ("nothing") into "something"; which is a product with full clinical utility that will help to improve health and well-being.The web site should use the visual feel of the logo (attached), be modern, simple and clean looking and represent creativity, innovation, scientific thinking and progress.
Updates

Wix Design is acceptable

Industry/Entity Type

Biotechnology

Coding

Coded - Design and coding required

Number of Pages Required

1 page

Font styles to use
Sans Serif

Requirements
Must have
• simple, clean look couple of pages
Should not have
• a lot of pages

```html
<!DOCTYPE html>
<html lang="en">
<head>
<meta charset="utf-8">
<title>Verantel Dx — Biotech Consulting Firm</title>
<link rel="stylesheet" href="https://fonts.googleapis.com/css2?family=Montserrat:ital,wght@0,400;0,500;0,600;0,700;0,800;1,400&display=swap">
<style>
:root{
  --blue:#1e88f0;
  --blue-deep:#0b57b5;
  --ink:#222;
  --text:#555;
  --line:#d9dde3;
  --panel:#f5f6f8;
  --footer:#262626;
  --footer-bar:#1a1a1a;
  --white:#fff;
}
*{box-sizing:border-box;margin:0;padding:0}
html,body{width:1200px;height:3143px;overflow:hidden}
body{position:relative;font-family:"Montserrat",sans-serif;color:var(--ink);background:var(--white)}
.abs{position:absolute}
.accent{color:var(--blue)}
.section-title{position:absolute;left:0;width:1200px;text-align:center;font-size:32px;font-weight:500}
.title-rule{position:absolute;left:578px;width:44px;height:2px;background:var(--blue)}

/* wordmark: name in one colour and weight, one plain square beside */
.wordmark{position:absolute;display:flex;align-items:center;gap:10px;white-space:nowrap;font-weight:500;color:var(--ink)}
.wordmark i{display:block;background:var(--blue)}

/* header */
.header-contact{position:absolute;top:14px;display:flex;align-items:center;gap:10px;font-size:18px}
.contact-badge{width:28px;height:28px;border:1.5px solid var(--blue);display:flex;align-items:center;justify-content:center}
.nav{position:absolute;top:72px;left:522px;display:flex;font-size:14px}
.nav a{color:var(--ink);text-decoration:none;display:block;padding:0 0 12px}
.nav a.active{color:var(--blue);border-bottom:2px solid var(--blue)}

/* hero */
.hero{position:absolute;top:106px;left:0;width:1200px;height:494px;background:linear-gradient(110deg,#c9d7e4 0%,#7e9fbd 35%,#3a6fa6 60%,#5e8fbf 80%,#a9c4dc 100%)}
.hero-frame{position:absolute;left:283px;top:296px;width:634px;height:126px;border:1.5px solid var(--white);border-top:none}
.hero-frame::before,.hero-frame::after{content:"";position:absolute;top:0;height:1.5px;background:var(--white);width:38px}
.hero-frame::before{left:0}.hero-frame::after{right:0}
.hero-title{position:absolute;top:272px;left:0;width:1200px;text-align:center;color:var(--white);font-size:40px;font-weight:800}
.hero-sub{position:absolute;top:330px;left:0;width:1200px;text-align:center;color:var(--white);font-size:16px;line-height:26px}
.btn{position:absolute;background:var(--blue);color:var(--white);font-size:13px;display:flex;align-items:center;justify-content:center;gap:8px;text-transform:uppercase}
.dots{position:absolute;left:0;width:1200px;display:flex;justify-content:center;gap:7px}
.dots i{width:8px;height:8px;border:1px solid var(--white)}
.dots i.on{background:var(--blue);border-color:var(--blue)}
.dots.dark i{border-color:var(--blue)}

/* about */
.about-frame{position:absolute;left:142px;top:671px;width:436px;height:401px;border:1.5px solid var(--blue)}
.about-photo{position:absolute;left:162px;top:692px;width:438px;height:359px;background:linear-gradient(135deg,#b8c9d8,#e6edf2 45%,#6b8a6a 70%,#d7e0e6)}
.about-title{position:absolute;left:686px;top:682px;font-size:32px;font-weight:500}
.about-lead{position:absolute;left:684px;top:750px;font-size:15px;font-weight:600}
.about-body{position:absolute;left:684px;top:776px;width:376px;font-size:11.5px;line-height:19px;color:var(--text)}
.feature{position:absolute;left:684px;width:390px}
.feature .ico{position:absolute;left:0;top:0;width:53px;height:53px;border:1.5px solid var(--blue);display:flex;align-items:center;justify-content:center}
.feature h3{position:absolute;left:73px;top:-2px;font-size:15px;font-weight:500}
.feature p{position:absolute;left:73px;top:22px;width:310px;font-size:11.5px;line-height:16px;color:var(--text)}
.link-more{position:absolute;color:var(--blue);font-size:13px;display:flex;align-items:center;gap:6px}

/* services */
.services-band{position:absolute;top:1143px;left:0;width:1200px;height:305px;background:linear-gradient(180deg,#0b4fa6,#0d5cbf)}
.services-band h2{position:absolute;top:62px;left:0;width:1200px;text-align:center;color:var(--white);font-size:32px;font-weight:500}
.services-band p{position:absolute;top:132px;left:0;width:1200px;text-align:center;color:var(--white);font-size:14.5px;font-weight:500}
.card{position:absolute;top:1324px;height:231px;background:var(--white);border:1.5px solid var(--blue);text-align:center}
.card.active{background:var(--blue);color:var(--white)}
.card .ico{position:absolute;top:28px;left:0;width:100%;display:flex;justify-content:center}
.card h3{position:absolute;top:114px;left:0;width:100%;font-size:16px;font-weight:600}
.card p{position:absolute;top:146px;left:14px;right:14px;font-size:11.5px;line-height:16px;color:var(--text)}
.card.active p{color:#e6f1ff}
.card .plus{position:absolute;bottom:-12px;left:50%;margin-left:-11px;width:22px;height:22px;background:var(--white);border:1.5px solid var(--blue);color:var(--blue);font-size:18px;line-height:18px}

/* why choose */
.why{position:absolute;top:1640px;left:0;width:1200px;height:502px;background:linear-gradient(120deg,#eef1f4,#f9fafb 50%,#f2efe9)}
.why-item{position:absolute;width:70px;height:70px;border:1.5px solid var(--blue);background:var(--white);display:flex;align-items:center;justify-content:center}
.why-item.filled{background:var(--blue)}
.why-label{position:absolute;font-size:14.5px;color:#333}
.why-label.left{text-align:right;width:200px}
.center-card{position:absolute;left:494px;top:1840px;width:212px;height:182px;background:var(--white);box-shadow:0 4px 18px rgba(0,0,0,.06);display:flex;align-items:center;justify-content:center}

/* reviews */
.arrow-box{position:absolute;width:30px;height:30px;border:1.5px solid var(--blue);display:flex;align-items:center;justify-content:center;background:var(--white)}
.arrow-box.grey{border-color:#aaa}
.quote-mark{position:absolute;top:2272px;left:0;width:1200px;text-align:center;font-size:72px;font-weight:800;color:#9cc3f0;line-height:1}
.quote{position:absolute;top:2336px;left:305px;width:590px;text-align:center;font-size:13.5px;line-height:22.5px;font-style:italic;color:var(--text)}
.reviewer{position:absolute;top:2417px;left:0;width:1200px;text-align:center;font-size:14px;font-weight:600}

/* partners */
.partners{position:absolute;top:2540px;left:0;width:1200px;height:318px;background:var(--panel)}
.partner{position:absolute;top:2690px;width:168px;height:97px;background:var(--white);border:1px solid #e4e6ea;display:flex;align-items:center;justify-content:center;gap:8px;font-size:20px;font-weight:600;color:#555}
.partner i{width:14px;height:14px;background:var(--blue)}

/* footer */
.footer{position:absolute;top:2858px;left:0;width:1200px;height:242px;background:var(--footer);color:var(--white)}
.footer h4{position:absolute;top:57px;font-size:15px;font-weight:500}
.footer .rule{position:absolute;top:84px;height:1px;background:#444}
.footer .rule b{display:block;width:30px;height:2px;background:var(--blue)}
.quick{position:absolute;top:98px;left:142px;list-style:none;font-size:11px;line-height:25.5px}
.quick li::before{content:"";display:inline-block;width:4px;height:4px;border:1px solid #777;margin-right:8px;vertical-align:middle}
.contact-row{position:absolute;left:332px;display:flex;gap:12px;font-size:11px;line-height:15px}
.contact-row svg{flex:none}
.newsletter-text{position:absolute;left:593px;top:92px;width:230px;font-size:10.5px;line-height:17px}
.field{position:absolute;left:593px;top:2991px;width:212px;height:32px;border:1px solid #555;font-size:11px;color:#999;padding:9px 10px}
.social{position:absolute;top:3033px;width:31px;height:31px;border:1.5px solid var(--white)}
.social.on{background:var(--blue);border-color:var(--blue)}
.copyright{position:absolute;top:3100px;left:0;width:1200px;height:43px;background:var(--footer-bar);color:#ddd;font-size:11px;text-align:center;line-height:43px}
</style>
</head>
<body>

<!-- Header -->
<div class="wordmark" style="left:142px;top:40px;font-size:19px"><i style="width:12px;height:12px"></i>Verantel Dx</div>
<div class="header-contact" style="left:727px"><span class="contact-badge"><svg width="14" height="14" viewBox="0 0 24 24"><path fill="#1e88f0" d="M6.6 10.8a15 15 0 0 0 6.6 6.6l2.2-2.2c.3-.3.7-.4 1-.2 1.1.4 2.3.6 3.6.6.6 0 1 .4 1 1V20c0 .6-.4 1-1 1A17 17 0 0 1 3 4c0-.6.4-1 1-1h3.5c.6 0 1 .4 1 1 0 1.3.2 2.5.6 3.6.1.3 0 .7-.2 1z"/></svg></span>555 014 2290</div>
<div class="header-contact" style="left:896px;font-size:14px"><span class="contact-badge"><svg width="14" height="12" viewBox="0 0 24 18"><path fill="#1e88f0" d="M0 0h24v2l-12 8L0 2zM0 5l12 8 12-8v13H0z"/></svg></span>info@veranteldx.com</div>
<nav class="nav">
  <a class="active" href="#" style="width:46px;text-align:center">Home</a>
  <a href="#" style="margin-left:52px">About Us</a>
  <a href="#" style="margin-left:60px">Services</a>
  <a href="#" style="margin-left:60px">Resources</a>
  <a href="#" style="margin-left:60px">Contact Us</a>
</nav>

<!-- Hero -->
<section class="hero" role="img" aria-label="Laboratory photo: scientist with pipette and glass flasks of blue liquid"></section>
<div class="hero-frame"></div>
<h1 class="hero-title">BIOTECH CONSULTING FIRM</h1>
<p class="hero-sub">We Serve Medical Diagnostics Industry, Which Is Part Of The<br>Life Science/healthcare Industry.</p>
<div class="btn" style="left:527px;top:403px;width:147px;height:38px">Read More <svg width="18" height="8" viewBox="0 0 18 8"><path d="M0 4h16M13 1l3 3-3 3" stroke="#fff" fill="none"/></svg></div>
<div class="dots" style="top:557px"><i class="on"></i><i></i><i></i><i></i></div>

<!-- About -->
<section class="about">
  <div class="about-frame"></div>
  <div class="about-photo" role="img" aria-label="Photo of a scientist placing a drop on a young plant in a petri dish"></div>
  <h2 class="about-title">About <span class="accent">Us</span></h2>
  <div class="abs" style="left:686px;top:730px;width:44px;height:2px;background:var(--blue)"></div>
  <div class="about-lead">Duis autem vel eum iriure dolor in hendrerit.</div>
  <p class="about-body">Lorem ipsum dolor sit amet, consectetuer adipiscing elit, sedmk diam nonummy nibh euismod tincidunt ut laoreet dolore magna aliquam erat volutpat. Suscipit lobortis nisl ut aliquip ex eamo kl commodo consequat.</p>
  <div class="feature" style="top:878px"><div class="ico"><svg width="30" height="30" viewBox="0 0 30 30" fill="none" stroke="#555" stroke-width="1.3"><circle cx="15" cy="15" r="12"/><circle cx="15" cy="15" r="7"/><circle cx="15" cy="15" r="2"/><path d="M15 15l10-10M22 5h3v3"/></svg></div><h3>Mission</h3><p>Accumsan et iusto odio dignissim qui blandit dollarl praesent luptatum zzril delenit augue.</p></div>
  <div class="feature" style="top:958px"><div class="ico"><svg width="32" height="22" viewBox="0 0 32 22" fill="none" stroke="#555" stroke-width="1.3"><path d="M1 11C8 1 24 1 31 11 24 21 8 21 1 11z"/><circle cx="16" cy="11" r="6"/><circle cx="16" cy="11" r="2.5"/></svg></div><h3>Vision</h3><p>Accumsan et iusto odio dignissim qui blandit dollarl praesent luptatum zzril delenit augue.</p></div>
  <div class="link-more" style="left:684px;top:1040px">READ MORE <svg width="18" height="8" viewBox="0 0 18 8"><path d="M0 4h16M13 1l3 3-3 3" stroke="#1e88f0" fill="none"/></svg></div>
</section>

<!-- Services -->
<section class="services-band" role="img" aria-label="Blue band with faint DNA helix background">
  <h2>Our Services</h2>
  <p>Lorem ipsum dolor sit amet, consectetuer adipiscing elit, sedmk diam nonummy nibh euismod.</p>
</section>
<div class="card active" style="left:142px;width:218px">
  <div class="ico"><svg width="56" height="56" viewBox="0 0 56 56" fill="none" stroke="#fff" stroke-width="1.5"><circle cx="20" cy="24" r="13"/><path d="M11 34L4 48"/><circle cx="38" cy="28" r="12"/><path d="M38 22v6l4 3M35 14h6"/></svg></div>
  <h3>Corporate Strategy</h3><p>Lorem ipsum dolor sit amet, consectetuer adipiscing elit, sedmk diam nonummy.</p><div class="plus">+</div>
</div>
<div class="card" style="left:378px;width:214px">
  <div class="ico"><svg width="56" height="56" viewBox="0 0 56 56" fill="none" stroke="#1e88f0" stroke-width="1.5"><path d="M28 28L8 20l20-8 20 8zM8 20v18l20 10 20-10V20M28 28v20"/><circle cx="28" cy="12" r="6"/><path d="M28 2v2M20 6l1 1M36 6l-1 1"/></svg></div>
  <h3>Product Development</h3><p>Lorem ipsum dolor sit amet, consectetuer adipiscing elit, sedmk diam nonummy.</p><div class="plus">+</div>
</div>
<div class="card" style="left:611px;width:215px">
  <div class="ico"><svg width="56" height="56" viewBox="0 0 56 56" fill="none" stroke="#1e88f0" stroke-width="1.5"><path d="M8 4h28l8 8v40H8z"/><circle cx="24" cy="30" r="8"/><circle cx="24" cy="30" r="3"/><circle cx="38" cy="30" r="5"/><path d="M14 46h24"/></svg></div>
  <h3>Business Development</h3><p>Lorem ipsum dolor sit amet, consectetuer adipiscing elit, sedmk diam nonummy.</p><div class="plus">+</div>
</div>
<div class="card" style="left:844px;width:214px">
  <div class="ico"><svg width="56" height="56" viewBox="0 0 56 56" fill="none" stroke="#1e88f0" stroke-width="1.5"><path d="M6 16h44l-4-10H10zM8 16v34h40V16M14 30h10v20H14zM30 28h12v12H30zM36 30v8M32 34h8"/></svg></div>
  <h3>Commercialization</h3><p>Lorem ipsum dolor sit amet, consectetuer adipiscing elit, sedmk diam nonummy.</p><div class="plus">+</div>
</div>

<!-- Why choose -->
<section class="why" role="img" aria-label="Faded laboratory background with capsules and heartbeat line"></section>
<div class="section-title" style="top:1696px">Why Choose <span class="accent">Us?</span></div>
<div class="title-rule" style="top:1745px"></div>
<svg class="abs" style="left:381px;top:1820px" width="438" height="210" fill="none" stroke="#b8c4d0" stroke-width="1">
  <path d="M0 5h56l56 50M0 111h113M0 217h56l56-50M437 5h-56l-56 50M437 111h-113M437 217h-56l-56-50"/>
</svg>
<div class="why-item filled" style="left:312px;top:1790px"><svg width="40" height="44" viewBox="0 0 40 44" fill="none" stroke="#fff" stroke-width="1.5"><circle cx="20" cy="18" r="14"/><circle cx="20" cy="18" r="9"/><path d="M15 18l4 4 6-7M10 29l-4 12 7-3 3 5 4-9M30 29l4 12-7-3-3 5-4-9"/></svg></div>
<div class="why-item" style="left:312px;top:1896px"><svg width="46" height="40" viewBox="0 0 46 40" fill="none" stroke="#555" stroke-width="1.3"><circle cx="23" cy="12" r="7"/><path d="M11 38c0-9 5-14 12-14s12 5 12 14"/><circle cx="9" cy="16" r="5"/><circle cx="37" cy="16" r="5"/><path d="M1 34c0-6 3-10 8-10M45 34c0-6-3-10-8-10"/></svg></div>
<div class="why-item" style="left:312px;top:2002px"><svg width="42" height="42" viewBox="0 0 42 42" fill="none" stroke="#555" stroke-width="1.3"><path d="M4 22l17 8 17-8v12l-17 7-17-7zM10 12h22l5 6-16 8-16-8z"/></svg></div>
<div class="why-label left" style="left:98px;top:1816px">Years Of Experience</div>
<div class="why-label left" style="left:98px;top:1922px">Proffesional Team</div>
<div class="why-label left" style="left:98px;top:2028px">Best Valuation</div>
<div class="why-item" style="left:818px;top:1790px"><svg width="40" height="40" viewBox="0 0 40 40" fill="none" stroke="#555" stroke-width="1.3"><path d="M6 36h28M10 32h20M20 32v-6M16 6l6-3 8 16-6 3z"/><circle cx="20" cy="26" r="3"/><path d="M26 22c6 2 6 10 0 12"/></svg></div>
<div class="why-item" style="left:818px;top:1896px"><svg width="44" height="44" viewBox="0 0 44 44" fill="none" stroke="#555" stroke-width="1.3"><circle cx="22" cy="22" r="19"/><circle cx="22" cy="22" r="15"/><path d="M22 11v11l7 5"/></svg></div>
<div class="why-item" style="left:818px;top:2002px"><svg width="42" height="44" viewBox="0 0 42 44" fill="none" stroke="#555" stroke-width="1.3"><circle cx="21" cy="16" r="9"/><path d="M10 16a11 11 0 0 1 22 0M9 14h3v6H9zM30 14h3v6h-3zM4 42c0-9 7-14 17-14s17 5 17 14"/></svg></div>
<div class="why-label" style="left:901px;top:1816px">Innovative Research</div>
<div class="why-label" style="left:901px;top:1922px">On Time Solutions</div>
<div class="why-label" style="left:901px;top:2028px">Start-up Support</div>
<div class="center-card"><span class="wordmark" style="position:static;font-size:26px">Verantel Dx</span></div>

<!-- Reviews -->
<div class="section-title" style="top:2198px">Customer <span class="accent">Reviews</span></div>
<div class="title-rule" style="top:2248px"></div>
<div class="quote-mark">&ldquo;</div>
<p class="quote">"Lorem ipsum dolor sit amet, consectetuer adipiscing elit, sedmk diam nonummy nibh euismod tincidunt ut laoreet dolore magna aliquam erat volutpat. Suscipit lobortis nisl ut aliquip ex eamo kl commodo consequat."</p>
<div class="reviewer">-Mr. Talen Brooke</div>
<div class="dots dark" style="top:2462px"><i class="on"></i><i></i><i></i><i></i></div>
<div class="arrow-box grey" style="left:142px;top:2373px"><svg width="10" height="16"><path d="M8 1L2 8l6 7" stroke="#999" fill="none"/></svg></div>
<div class="arrow-box" style="left:1028px;top:2373px"><svg width="10" height="16"><path d="M2 1l6 7-6 7" stroke="#1e88f0" fill="none"/></svg></div>

<!-- Partners -->
<section class="partners"></section>
<div class="section-title" style="top:2603px">Our <span class="accent">Parteners</span></div>
<div class="title-rule" style="top:2652px"></div>
<div class="partner" style="left:142px"><i></i>Norlane</div>
<div class="partner" style="left:329px">Pellucid</div>
<div class="partner" style="left:516px">Fernway</div>
<div class="partner" style="left:703px">Ironmill</div>
<div class="partner" style="left:890px">Tallbox</div>
<div class="arrow-box grey" style="left:71px;top:2723px"><svg width="10" height="16"><path d="M8 1L2 8l6 7" stroke="#999" fill="none"/></svg></div>
<div class="arrow-box" style="left:1099px;top:2723px"><svg width="10" height="16"><path d="M2 1l6 7-6 7" stroke="#1e88f0" fill="none"/></svg></div>

<!-- Footer -->
<footer class="footer">
  <h4 style="left:142px">Quick <span class="accent">Links</span></h4>
  <div class="rule" style="left:142px;width:155px"><b></b></div>
  <ul class="quick"><li>Home</li><li>About Us</li><li>Services</li><li>Resources</li><li>Contact Us</li></ul>
  <h4 style="left:332px">Contact <span class="accent">Detail</span></h4>
  <div class="rule" style="left:332px;width:164px"><b></b></div>
  <div class="contact-row" style="top:100px"><svg width="12" height="16" viewBox="0 0 12 16"><path d="M6 15S1 9 1 6a5 5 0 0 1 10 0c0 3-5 9-5 9z" stroke="#aaa" fill="none"/><circle cx="6" cy="6" r="2" stroke="#aaa" fill="none"/></svg><div><b style="font-weight:600">Verantel Dx</b><br><span style="font-size:10px">45, Orchard Lane,<br>Brentvale, AB-204 118</span></div></div>
  <div class="contact-row" style="top:164px;font-size:13px"><svg width="14" height="14" viewBox="0 0 24 24"><path fill="none" stroke="#aaa" stroke-width="1.5" d="M6.6 10.8a15 15 0 0 0 6.6 6.6l2.2-2.2 4.6 1V20A17 17 0 0 1 3 4h4.5l1 4.6z"/></svg>555 014 2290</div>
  <div class="contact-row" style="top:195px"><svg width="14" height="11" viewBox="0 0 24 18"><path d="M1 1h22v16H1zM1 1l11 8 11-8" stroke="#aaa" fill="none" stroke-width="1.5"/></svg>info@veranteldx.com</div>
  <h4 style="left:593px">Newsletter <span class="accent">Signup</span></h4>
  <div class="rule" style="left:593px;width:212px"><b></b></div>
  <p class="newsletter-text">Lorem ipsum dolor sit amet, consectetu<br>adipiscing elit, sedmk nonummy.</p>
</footer>
<div class="field">Email</div>
<div class="btn" style="left:593px;top:3033px;width:106px;height:30px;font-size:12px">Submit <svg width="14" height="8" viewBox="0 0 14 8"><path d="M0 4h12M9 1l3 3-3 3" stroke="#fff" fill="none"/></svg></div>
<div class="wordmark" style="left:925px;top:2944px;font-size:20px;color:var(--white)">Verantel Dx</div>
<div class="social on" style="left:900px"></div>
<div class="social" style="left:942px"></div>
<div class="social" style="left:985px"></div>
<div class="social" style="left:1027px"></div>
<div class="copyright">Copyright &nbsp;2019 - Verantel Dx. All Rights Reserved.</div>

</body>
</html>
```